Visitenkarten-Design für Garten- und Landschaftspflege
Nerapo Kulm setzte meine Vorstellungen absolut super um ich kann Ihn nur weiter empfehlen. vielen dank
Zielgruppe
Baumpflege, Baumfällung, Garten und Landschaftspflege meine zielgruppe sind Privatpersonen im alter von 20-100Jahren
Aufgabenstellung
Sehr geehrte Damen und Herren, die visitenkarte sollte die angaben so enthalten wie sie auf der von mir gestallteten Visitenkarten sind ( meine ist kein maß der Dinge). Ich habe mein Logo leider nur als 3.jpg Datei. Das Logo darf im Design erändert werden aber bitte nur Feinheiten ansonsten stehen ihnen alle türen offen um kreativ zu sein.
mit freundlichen Grüßen Jonas Vehmar

```html
<!DOCTYPE html>
<html lang="de">
<head>
<meta charset="utf-8">
<title>Visitenkarte Baumpflege Vehmar</title>
<link rel="stylesheet" href="https://fonts.googleapis.com/css2?family=Barlow:wght@400;500&display=swap">
<style>
  :root {
    --paper: #ffffff;
    --ink: #111111;
    --leaf: #a5c443;
    --accent: #b3343c;
    --edge: #9a9a9a;
  }
  * { box-sizing: border-box; margin: 0; padding: 0; }
  html, body {
    width: 1200px; height: 874px; overflow: hidden;
    background: var(--paper);
    font-family: "Barlow", sans-serif;
  }
  .card {
    position: absolute; top: 115px;
    width: 414px; height: 638px;
    background: var(--paper);
    border: 1px solid var(--edge);
    box-shadow: 10px 14px 18px rgba(0,0,0,0.18);
    overflow: hidden;
  }
  .card--front { left: 118px; }
  .card--back { left: 613px; }

  .brand {
    position: absolute; left: 0; top: 0; width: 100%; height: 314px;
    display: flex; align-items: center; justify-content: center; gap: 14px;
  }
  .brand-mark { width: 22px; height: 22px; background: var(--ink); }
  .brand-name {
    color: var(--ink); font-weight: 500; font-size: 34px;
    letter-spacing: 1px; line-height: 40px;
  }

  .green-field {
    position: absolute; left: 0; bottom: 0; width: 100%;
    background: var(--leaf);
  }
  .card--front .green-field { top: 314px; padding: 18px 0 0 38px; }
  .card--back .green-field { top: 140px; border-top: 4px solid var(--ink); padding: 44px 0 0 38px; }

  .person-name { color: var(--accent); font-size: 31px; font-weight: 400; line-height: 36px; }
  .person-role { color: var(--ink); font-size: 20px; line-height: 23px; margin-top: 4px; }
  .contact { color: var(--paper); font-size: 22px; line-height: 31px; margin-top: 10px; font-style: normal; }

  .services-title { color: var(--accent); font-size: 31px; font-weight: 400; line-height: 36px; }
  .services { list-style: none; margin-top: 16px; }
  .services li {
    color: var(--paper); font-size: 20.5px; line-height: 31.5px;
    padding-left: 25px; position: relative;
  }
  .services li::before {
    content: ""; position: absolute; left: 3px; top: 12px;
    width: 8px; height: 8px; border-radius: 50%; background: var(--paper);
  }
</style>
</head>
<body>
  <section class="card card--front">
    <div class="brand">
      <span class="brand-mark"></span>
      <span class="brand-name">Baumpflege Vehmar</span>
    </div>
    <div class="green-field">
      <h1 class="person-name">Jonas Vehmar</h1>
      <p class="person-role">Fachagrarwirt<br>Baumpflege &amp; -sanierung</p>
      <address class="contact">
        Ahornstraße 12<br>
        84712 Feldmoos<br>
        Telefon 0170 555 24 18<br>
        kontakt@baumpflege-vehmar.de<br>
        baumpflege-vehmar.de
      </address>
    </div>
  </section>

  <section class="card card--back">
    <div class="green-field">
      <h2 class="services-title">Unsere Leistungen</h2>
      <ul class="services">
        <li>Neu-Pflanzungen</li>
        <li>Herstellen der Verkehrs-<br>sicherheit von Bäumen</li>
        <li>Kronenrückschnitt<br>(Einkürzung und Kronenpflege)</li>
        <li>Prüfen von Bäumen auf<br>Stansicherheit</li>
        <li>Fällen von Bäumen</li>
        <li>Fräsen von Wurzelstöcken</li>
        <li>Anbau und Fertigung von<br>Gartenhäusern nach Maß</li>
      </ul>
    </div>
  </section>
</body>
</html>
```